Design a Job Application & CV

I need a design for upcoming job applications that includes a cv. It needs to look as elegant and modern as possible as the application will be send mainly to large corporations and strategy consultancies. I have attached an application that I like for your consideration. One of the more difficult requirements is that it needs to be editable in ms office word for mac/windows.
As stated only the design is part of this project. I will fill in my content later on.
Reason: Dear Designers,
I am going to increase the budget as well as extending the deadline. I am hoping that you can improve upon the design that I have provided in the brief. If you have questions please let me know.
Dear Designers,
Target Market(s)
Human Resources Managers, Senior Consultants and Executives of larger firms
Industry/Entity Type
Office
Requirements
Must have
- 4 Pages including( a cover page, a coverletter page, 2 pages cv)
It should be easy to edit and should be readable by word for mac, i.e. in the *.docx format.
Here is an example of what I like:
http://www.torvenmald.example/applicationexample.pdf
http://www.torvenmald.example/applicationExample.docx
colors that I like are blue, grey, black, white
Nice to have
- icons to indicate sections
Should not have
- invasive cliparts

```html
<!DOCTYPE html>
<html lang="en">
<head>
<meta charset="utf-8">
<title>My Goal/Vision – Cover</title>
<link rel="stylesheet" href="https://fonts.googleapis.com/css2?family=Cagliostro&display=swap">
<style>
  :root {
    --page-dark: #3f3f41;
    --page-light: #6a6a6c;
    --accent-blue: #0aa6dd;
    --text-white: #ffffff;
    --rule-white: rgba(255, 255, 255, 0.85);
  }
  html, body {
    margin: 0;
    padding: 0;
    overflow: hidden;
    background: var(--page-dark);
  }
  .cover {
    position: relative;
    width: 848px;
    height: 1200px;
    overflow: hidden;
    background: linear-gradient(90deg, var(--page-dark) 0%, var(--page-light) 100%);
    font-family: "Cagliostro", sans-serif;
    color: var(--text-white);
  }
  .cover-title {
    position: absolute;
    left: 72px;
    top: 252px;
    margin: 0;
    font-weight: 400;
    font-size: 76px;
    line-height: 1;
    letter-spacing: -0.5px;
  }
  .motto-band {
    position: absolute;
    left: 0;
    top: 404px;
    width: 848px;
    height: 150px;
    background: var(--accent-blue);
  }
  .motto-rule {
    position: absolute;
    left: 0;
    width: 848px;
    border-top: 2px dotted var(--rule-white);
  }
  .motto-rule--top { top: 36px; }
  .motto-rule--bottom { top: 104px; }
  .motto-text {
    position: absolute;
    left: 72px;
    top: 46px;
    margin: 0;
    font-size: 37px;
    line-height: 1.2;
    white-space: nowrap;
  }
  .footer-band {
    position: absolute;
    left: 0;
    top: 1124px;
    width: 848px;
    height: 32px;
    background: var(--accent-blue);
  }
</style>
</head>
<body>
  <main class="cover">
    <h1 class="cover-title">My Goal/Vision</h1>
    <section class="motto-band">
      <div class="motto-rule motto-rule--top"></div>
      <p class="motto-text">Looking Good and Working Hard is my style!</p>
      <div class="motto-rule motto-rule--bottom"></div>
    </section>
    <div class="footer-band"></div>
  </main>
</body>
</html>
```